website re-design - the brickleaf studio

The Brickleaf Studio is an existing website that we built using a new zealand based online CMS tool which is quite flexible and accomodates custom designs. You can check it here: http://www.pagecrafter.example.nz/.

We have a logo already and the content on the website is OK.
The website can be found at www.thebrickleafstudio.example.au

mainly the homepage, but if the design is easily adapted to the other pages then, we will commission the winner to update these pages also.
Updates

Hi there,  I am uploading an image to be used as the main image on the homepage design,  so all submissions have the same image.

Target Market(s)

property developers, architects, builders, home buyers

Industry/Entity Type

Shop

Requirements
Must have
• Must utilise the existing CMS or at least be compatible to upload
Nice to have
• a promotional banner that can be turned off and on and changed as required as we offer different promotions over time.

```html
<!DOCTYPE html>
<html lang="en">
<head>
<meta charset="utf-8">
<title>The Brickleaf Studio – Architectural Scale Models</title>
<link rel="stylesheet" href="https://fonts.googleapis.com/css2?family=Arimo:wght@400;700&family=Questrial&family=Fjalla+One&display=swap">
<style>
  :root{
    --side-bg:#262626;
    --side-bg-2:#2e2e2e;
    --main-bg:#e4e4e4;
    --footer-bg:#282828;
    --orange:#f08a12;
    --orange-dark:#d86e00;
    --text:#2b2b2b;
    --muted:#b9b9b9;
    --footer-text:#8a8a8a;
    --nav-bg:#3a3a3a;
    --blue:#1a8df0;
    --green:#46c12a;
  }
  *{box-sizing:border-box;margin:0;padding:0}
  html,body{width:1025px;height:1200px;overflow:hidden}
  body{position:relative;background:var(--main-bg);font-family:"Arimo",Arial,sans-serif;color:var(--text)}
  .sidebar{position:absolute;left:0;top:0;width:305px;height:1113px;background:repeating-linear-gradient(45deg,var(--side-bg) 0 2px,var(--side-bg-2) 2px 4px)}
  .footer{position:absolute;left:0;top:1113px;width:1025px;height:87px;background:repeating-linear-gradient(45deg,var(--side-bg) 0 2px,var(--side-bg-2) 2px 4px);text-align:center;padding-top:34px;font-size:12px;color:var(--footer-text)}
  .search{position:absolute;left:68px;top:101px;width:224px;height:28px;display:flex}
  .search-field{flex:1;background:#1a1a1a;border:1px solid #3c3c3c;color:#777;font-size:12px;padding:7px 8px}
  .search-button{width:30px;background:var(--orange);display:flex;align-items:center;justify-content:center}
  .brand-band{position:absolute;left:32px;top:143px;width:273px;height:40px;background:linear-gradient(#f9a32b,var(--orange-dark));border-radius:6px 0 0 6px;font-family:"Fjalla One",sans-serif;font-size:19px;color:#2a2a2a;padding:8px 0 0 44px;white-space:nowrap}
  .intro-side{position:absolute;left:60px;top:218px;width:232px;text-align:right;font-size:19.5px;line-height:25.5px;color:var(--muted);font-weight:400}
  .side-heading{position:absolute;right:18px;font-family:"Questrial",sans-serif;font-size:22px;color:var(--orange)}
  .field{position:absolute;left:60px;width:224px;height:28px;background:#1a1a1a;border:1px solid #3a3a3a;color:#8a8a8a;font-size:12px;padding:7px 10px}
  .subscribe{position:absolute;left:188px;top:660px;width:95px;height:29px;background:linear-gradient(#35aaff,#0c79d8);border-radius:2px;font-family:"Fjalla One",sans-serif;font-size:14px;color:#10305a;text-align:center;padding-top:5px;letter-spacing:.5px}
  .map{position:absolute;left:48px;top:779px;width:241px;height:110px;background:linear-gradient(135deg,#e8e4d8,#d7dccf 55%,#a9c4dd);border:2px solid #fff}
  .divider{position:absolute;left:48px;top:910px;width:243px;height:1px;background:#555}
  .address{position:absolute;right:14px;top:930px;text-align:right;font-size:12px;line-height:13.6px;color:var(--muted);font-style:normal}
  .address a{color:var(--orange);text-decoration:none}
  .social{position:absolute;left:82px;top:1075px;display:flex;gap:7px}
  .social span{width:37px;height:37px;border-radius:7px;background:linear-gradient(#f2f2f2,#a9a9a9);border:2px solid #555}
  .masthead{position:absolute;left:327px;top:36px;display:flex;align-items:center;gap:18px}
  .masthead-mark{width:140px;height:74px;background:var(--orange)}
  .masthead-name{font-family:"Questrial",sans-serif;font-size:32px;color:#222;line-height:1}
  .masthead-tag{font-family:"Questrial",sans-serif;font-size:15px;color:var(--orange);letter-spacing:.6px;margin-top:4px}
  .nav{position:absolute;left:305px;top:141px;width:689px;height:41px;background:linear-gradient(#4a4a4a,#2a2a2a);border-radius:0 8px 8px 0;display:flex;align-items:center;padding-left:10px;gap:4px;box-shadow:0 4px 6px rgba(0,0,0,.25)}
  .nav a{font-size:12.5px;color:#eee;text-decoration:none;padding:6px 8px}
  .nav a.current{background:#1c1c1c;border-radius:3px;border:1px solid #555}
  .hero{position:absolute;left:325px;top:203px;width:644px;height:361px;border:3px solid #ccc;background:linear-gradient(160deg,#3c4a40 0%,#6e7a6d 35%,#b6a79a 55%,#4b5b4e 80%,#222 100%)}
  .content{position:absolute;left:326px;top:592px;width:650px;font-size:12px;line-height:14.6px}
  .content p{margin-bottom:14px}
  .questions{color:var(--orange);list-style:none;margin-bottom:14px}
  .steps{margin:0 0 14px 22px}
  .cta{position:absolute;top:916px;height:64px;border-radius:4px;font-family:"Fjalla One",sans-serif;font-size:31px;text-align:center;padding-top:10px;box-shadow:0 6px 6px -3px rgba(0,0,0,.35)}
  .cta-order{left:373px;width:214px;background:linear-gradient(#39b2ff,#0b73dd);color:#0d2f66}
  .cta-quote{left:688px;width:213px;background:linear-gradient(#6ee04a,#2fa514);color:#12420a}
  .cta-or{position:absolute;left:622px;top:932px;font-family:"Fjalla One",sans-serif;font-size:25px;color:#444}
</style>
</head>
<body>
  <aside class="sidebar">
    <div class="search">
      <div class="search-field">search</div>
      <div class="search-button">
        <svg width="18" height="18" viewBox="0 0 18 18"><circle cx="7" cy="7" r="5" fill="none" stroke="#fff" stroke-width="2"/><line x1="11" y1="11" x2="16" y2="16" stroke="#fff" stroke-width="3"/></svg>
      </div>
    </div>
    <div class="brand-band">THE BRICKLEAF STUDIO</div>
    <p class="intro-side">Getting an architectural model produced can be expensive and time consuming, but it can also add a lot of value to a project. A scale model lets everyone involved, get a very clear understanding of your building.</p>

    <h2 class="side-heading" style="top:544px">NEWSLETTER</h2>
    <div class="field" style="top:577px">Your name</div>
    <div class="field" style="top:619px">Email</div>
    <div class="subscribe">SUBSCRIBE</div>

    <h2 class="side-heading" style="top:734px">CONTACT</h2>
    <div class="map" role="img" aria-label="Street map showing the studio location"></div>
    <div class="divider"></div>
    <address class="address">
      14 Fernhill Lane Number 9<br>Springvale 40118<br>Block C-101<br><br>
      Phone: 555-010-203<br>Fax: 555-010-204<br>
      Email: <a href="#">hello@brickleaf.example</a><br>
      Website: <a href="#">www.brickleaf.example</a>
    </address>
    <div class="social"><span></span><span></span><span></span><span></span><span></span></div>
  </aside>

  <header class="masthead">
    <div class="masthead-mark"></div>
    <div>
      <div class="masthead-name">THE BRICKLEAF STUDIO</div>
      <div class="masthead-tag">ARCHITECTURAL SCALE MODELS</div>
    </div>
  </header>

  <nav class="nav">
    <a class="current" href="#">Home</a><a href="#">Gallery</a><a href="#">Order Online</a><a href="#">Get a Quote</a><a href="#">Contact</a><a href="#">3D Visualisation</a><a href="#">About Us</a><a href="#">Sitemap</a>
  </nav>

  <div class="hero" role="img" aria-label="Architectural scale model of a residential development with houses, apartment blocks and trees"></div>

  <main class="content">
    <p>&nbsp;If you answered yes to any of the following questions, then you should be using the brickleaf studio.</p>
    <ul class="questions">
      <li>Are you undertaking a new apartment development or land development and need a model for council approval or marketing purposes?</li>
      <li>Are you getting a new house designed and built and need a clear understanding of how it will look?</li>
      <li>Are you an architect or building designer looking for a more affordable way to add to your service?</li>
      <li>Are you wanting to clarify in your own mind how your new building sits on its site?</li>
      <li>Are you looking to for a way to market your buildings in an effective and affordable format that everyone can relate to?</li>
    </ul>
    <p style="margin-bottom:8px">It's this easy</p>
    <ol class="steps">
      <li>Order online or fill in the quote form.</li>
      <li>We'll build your model and deliver it right to your door.</li>
    </ol>
    <p>You can tailor your model to suit your project and budget needs. There are various add-ons such as a display case, internal walls, acrylic windows, people trees and cars and site contours as well as a scaled pricing structure based on the size of your building.</p>
    <p>We have made the system very easy to use, so all you need to do is click your way to your new scale model. Just follow the prompts and away you go. Click here to order your model now. Or click here to get a quote.</p>
  </main>

  <a class="cta cta-order">ORDER NOW</a>
  <span class="cta-or">OR</span>
  <a class="cta cta-quote">GET A QUOTE</a>

  <footer class="footer">2011 © Copyright The Brickleaf Studio - Site map Phone: (08) 5550 0142 Australia</footer>
</body>
</html>
```